Business Cards Design for the electrical wholesaler: clean bold dynamic :)

We need a business card design that would follow our latest brand guidelines. As an electrical wholesaler we want to bring a fresh look and feel into the industry. The design should be clean bold and dynamic. It should come alive with the renewed energy of our green colour. Our grey colour should keep things balanced and complement the notion of maturity and responsibility. We employ Lato as a corporate font however are not bound by this font and we’re open to interpretation here.

Target Market(s)

Electrical contractors

Industry/Entity Type

Business

Contact Information for Business Card

Logo
Name & Surname: Halyna Dorosh
Job Title: Director of Marketing
Email: halya.dorosh@quillmail.example
Cell phone: XXX.XXX.XXXX
Address: 20517 - 87 Ave. Edmonton, AB, Canada. T6K 4N8
Business Phone: 780.555.0184
Website: www.brovix.example

Font styles to use
Other font styles liked:
• Lato

Requirements
Must have
• Logo & website
Nice to have
• Brand elements - some of them you may find in the attached Brand Guidelines (e.g. three lines on the background signifying "W")

```html
<!DOCTYPE html>
<html lang="en">
<head>
<meta charset="utf-8">
<title>Brovix Business Cards</title>
<link rel="stylesheet" href="https://fonts.googleapis.com/css2?family=Lato:wght@400;700;900&display=swap">
<style>
  :root {
    --backdrop: #2b2b2c;
    --brand-green: #7dbb3c;
    --brand-grey: #4b4b4d;
    --card-white: #f3f3f2;
    --ink-light: #ffffff;
  }
  * { margin: 0; padding: 0; box-sizing: border-box; }
  html, body {
    width: 1200px; height: 960px; overflow: hidden;
    background: var(--backdrop);
    font-family: "Lato", Arial, sans-serif;
  }
  .canvas { position: relative; width: 1200px; height: 960px; }
  .card {
    position: absolute; width: 600px; height: 342px;
    border-radius: 22px; overflow: hidden;
    box-shadow: 0 6px 14px rgba(0,0,0,.45);
  }
  .card--front { left: 314px; top: 113px; background: var(--card-white); }
  .card--back { left: 311px; top: 472px; background: var(--brand-green); }

  .front-panel { position: absolute; inset: 0; }

  .wordmark {
    position: absolute; display: flex; align-items: center; gap: 12px;
    font-weight: 700; letter-spacing: -1px; line-height: 1;
  }
  .wordmark__square { width: 34px; height: 34px; border-radius: 3px; }
  .card--front .wordmark { left: 52px; top: 139px; font-size: 62px; color: var(--brand-grey); }
  .card--front .wordmark__square { background: var(--brand-green); }
  .card--back .wordmark { left: 0; right: 0; top: 137px; justify-content: center; font-size: 66px; color: var(--ink-light); }
  .card--back .wordmark__square { background: var(--ink-light); }

  .contact {
    position: absolute; left: 374px; top: 72px; color: var(--ink-light);
  }
  .contact__name { font-size: 20px; font-weight: 700; line-height: 1.1; text-transform: uppercase; }
  .contact__title { font-size: 15px; line-height: 1.3; text-transform: uppercase; }
  .contact__address { margin-top: 13px; font-size: 14px; line-height: 1.3; }
  .contact__list { margin-top: 12px; list-style: none; font-size: 13.5px; line-height: 19px; }
  .contact__list li { display: flex; align-items: center; gap: 8px; white-space: nowrap; }
  .contact__list svg { width: 14px; height: 14px; fill: var(--ink-light); flex: none; }

  .back-url {
    position: absolute; left: 0; right: 0; top: 292px; text-align: center;
    color: var(--ink-light); font-size: 13px; letter-spacing: 3.4px;
  }
</style>
</head>
<body>
<main class="canvas">
  <section class="card card--front" aria-label="Business card front">
    <svg class="front-panel" viewBox="0 0 600 342" aria-hidden="true">
      <path d="M206 0 C245 0 268 35 288 95 L343 262 C362 318 392 342 428 342 L600 342 L600 0 Z" fill="var(--brand-green)"/>
    </svg>
    <div class="wordmark"><span class="wordmark__square"></span>brovix</div>
    <div class="contact">
      <p class="contact__name">Halyna Dorosh</p>
      <p class="contact__title">CEO/Founder</p>
      <p class="contact__address">20517 - 87 Ave.<br>Edmonton, AB, Canada. T6K 4N8</p>
      <ul class="contact__list">
        <li><svg viewBox="0 0 16 16"><path d="M3.6 1.2l2.3 2.6-1.3 2a8.5 8.5 0 0 0 5.6 5.6l2-1.3 2.6 2.3-1.5 2.4C7.8 16.6-.6 8.2 1.2 2.7z"/></svg>780.555.0184</li>
        <li><svg viewBox="0 0 16 16"><path d="M4 0h8a1 1 0 0 1 1 1v14a1 1 0 0 1-1 1H4a1 1 0 0 1-1-1V1a1 1 0 0 1 1-1zm1 2v10h6V2zm3 11a1 1 0 1 0 0 2 1 1 0 0 0 0-2z"/></svg>780.555.0127</li>
        <li><svg viewBox="0 0 16 16"><path d="M4 1h8v4H4zM1 6h14v7h-3v2H4v-2H1zm4 5v3h6v-3z"/></svg>780.555.0199</li>
        <li><svg viewBox="0 0 16 16"><path d="M1 3h14v10H1zm1.5 1.2L8 8.6l5.5-4.4z"/></svg>halya.dorosh@quillmail.example</li>
        <li><svg viewBox="0 0 16 16"><path d="M8 1a7 7 0 1 0 0 14A7 7 0 0 0 8 1zm-1 2.2c-.6 1-1.6 1.4-1.2 2.6.5 1.3 2.2.8 2.4 2.2.1 1-1 1.6-.6 3 .2.7.8 1.3 1.5 1.5A5.6 5.6 0 0 1 3 6.3c1 .2 2-.6 4-3.1zm3.6 1c1 .9 1.9 2.3 2 3.9-1-.3-1.5-1-2.5-.5-.8.4-1.5-.6-.9-1.4.5-.6 1.4-.9 1.4-2z"/></svg>www.brovix.example</li>
      </ul>
    </div>
  </section>

  <section class="card card--back" aria-label="Business card back">
    <div class="wordmark"><span class="wordmark__square"></span>brovix</div>
    <p class="back-url">www.brovix.example</p>
  </section>
</main>
</body>
</html>
```